KTWG application splash screen

We need a 1024x768 image for use as an application splash screen.
The image will be displayed full screen on an 10 inch industrial PC 1024x768 screen while our application is launching. The image should convey that the application is "Waiting for connection to Wi-Fi access point..." and include a graphic of the industrial PC connected to the access point via an Ethernet cable. A list of troubleshooting steps should be included at the bottom of the image. The troubleshooting steps should not be the main focus of the image and should be shown in a smaller font (but still readable at 1024x768 displayed on a 10 inch screen).
I will include a mock up of the general idea of what we are looking for as well as image files for the industrial PC, a screenshot of our application to show on the PC's screen and the AP.
For general look and feel and a sense of corporate branding please review our website https://marrowgatesoilworks.example/. The splash screen should reflect corporate branding.
Target Market(s)
Users of our application
Industry/Entity Type
Agriculture
Look and feel

```html
<!DOCTYPE html>
<html lang="en">
<head>
<meta charset="utf-8">
<title>KTWG Splash Screen – Waiting for Wi-Fi</title>
<link href="https://fonts.googleapis.com/css2?family=Lexend:wght@600;700&family=Poppins:wght@400;500;600;700&display=swap" rel="stylesheet">
<style>
  :root{
    --green:#42bd6b;
    --green-bright:#5fe08a;
    --green-deep:#1f7a43;
    --dark:#17201a;
    --dark-2:#223027;
    --white:#ffffff;
    --page:#000000;
  }
  *{margin:0;padding:0;box-sizing:border-box}
  html,body{width:1200px;height:1200px;overflow:hidden;background:var(--page)}
  .splash{
    position:absolute;left:110px;top:233px;width:979px;height:734px;
    background:var(--white);overflow:hidden;
    font-family:"Poppins",sans-serif;
  }
  .band{position:absolute;left:0;width:979px}
  .band-top{top:0;height:197px}
  .band-bottom{top:547px;height:187px}
  .band-art{position:absolute;inset:0}
  .band-top .band-art{
    background:
      radial-gradient(ellipse 260px 200px at 860px 80px, rgba(120,240,160,.75), transparent 70%),
      radial-gradient(ellipse 200px 150px at 90px 40px, rgba(95,224,138,.55), transparent 70%),
      linear-gradient(100deg,#3fae63 0%,#2e8a4e 28%,var(--dark) 45%,var(--dark-2) 62%,#2f9455 78%,#5bd684 100%);
  }
  .band-bottom .band-art{
    background:
      radial-gradient(ellipse 220px 180px at 140px 150px, rgba(110,235,150,.8), transparent 70%),
      radial-gradient(ellipse 180px 110px at 900px 150px, rgba(63,174,99,.8), transparent 70%),
      linear-gradient(100deg,#4cc874 0%,#2e9a55 25%,var(--dark) 45%,var(--dark-2) 70%,#2f8f52 88%,#3fae63 100%);
  }
  .title-card{
    position:absolute;left:283px;top:0;width:413px;height:163px;
    background:var(--white);border-radius:0 0 19px 19px;
    display:flex;align-items:center;justify-content:center;padding-top:8px;
  }
  .title{
    font-family:"Lexend",sans-serif;font-weight:700;color:var(--green);
    font-size:33px;line-height:34px;text-align:center;letter-spacing:1px;
  }
  .device{
    position:absolute;width:262px;height:262px;border-radius:50%;
    background:var(--green);top:238px;
  }
  .device-cab{left:52px}
  .device-ap{left:665px}
  .device-art{position:absolute}
  .cab-art{left:42px;top:26px;width:178px;height:141px;border-radius:10px;
    background:linear-gradient(180deg,#2a2a2a,#111);border:3px solid #3a3a3a}
  .cab-art::after{content:"";position:absolute;left:14px;top:12px;right:14px;bottom:18px;border-radius:2px;
    background:linear-gradient(180deg,#f4f6f5 0%,#e6ece8 55%,#9fd9b2 56%,#d8efe0 100%)}
  .ap-art{left:121px;top:23px;width:21px;height:147px;border-radius:6px;
    background:linear-gradient(90deg,#e9eeec,#ffffff 50%,#dfe5e2)}
  .device-label{
    position:absolute;left:0;right:0;top:180px;text-align:center;color:var(--white);
  }
  .device-name{font-weight:600;font-size:18px;letter-spacing:1.2px;line-height:22px}
  .device-model{font-weight:400;font-size:13px;letter-spacing:1px;line-height:18px}
  .device-ap .device-model{font-size:11.5px;letter-spacing:.6px}
  .cable{position:absolute;left:337px;top:366px;width:306px;height:8px}
  .cable-label{
    position:absolute;left:0;width:979px;top:382px;text-align:center;
    font-weight:600;font-size:20px;letter-spacing:1.4px;color:var(--green);
  }
  .help-card{
    position:absolute;left:277px;top:579px;width:426px;height:155px;
    background:var(--white);border-radius:16px 16px 0 0;
    color:var(--green);padding:10px 10px 0 24px;
  }
  .help-title{font-weight:600;font-size:14.5px;letter-spacing:1px;text-align:center;margin-bottom:4px}
  .help-list{list-style:none;font-size:10.8px;line-height:12.4px;letter-spacing:-.1px}
  .help-list li{padding-left:7px;text-indent:-7px}
  .help-list li::before{content:"• "}
  .help-list ul{list-style:none;margin-left:12px}
  .brand{
    position:absolute;left:857px;top:68px;width:88px;height:88px;
    display:flex;align-items:center;justify-content:center;gap:6px;
    font-family:"Poppins",sans-serif;font-weight:700;font-size:22px;color:var(--white);letter-spacing:.5px;
  }
  .brand-square{width:12px;height:12px;background:var(--white)}
</style>
</head>
<body>
<main class="splash">
  <header class="band band-top">
    <div class="band-art" role="img" aria-label="Green and dark technology-style background with circuit lines and glowing dots"></div>
    <div class="title-card">
      <h1 class="title">Waiting for<br>connection to Wi-Fi<br>access point...</h1>
    </div>
  </header>

  <section class="device device-cab">
    <div class="device-art cab-art" role="img" aria-label="Industrial tablet PC showing the KTWG seeding application"></div>
    <div class="device-label">
      <div class="device-name">TRACTOR CAB</div>
      <div class="device-model">COMPUTER</div>
    </div>
  </section>

  <svg class="cable" viewBox="0 0 306 8" aria-hidden="true">
    <line x1="3" y1="4" x2="304" y2="4" stroke="#42bd6b" stroke-width="4.4" stroke-linecap="round" stroke-dasharray="0 10.4"/>
  </svg>
  <div class="cable-label">ETHERNET CABLE</div>

  <section class="device device-ap">
    <div class="device-art ap-art" role="img" aria-label="White outdoor Wi-Fi access point with two antennas"></div>
    <div class="device-label">
      <div class="device-name">WI-FI ACCESS POINT</div>
      <div class="device-model">NETVALE AX-220 OUTDOOR</div>
    </div>
  </section>

  <footer class="band band-bottom">
    <div class="band-art" role="img" aria-label="Green and dark technology-style background with dotted waves and circuit lines"></div>
    <div class="brand"><span class="brand-square"></span>KTWG</div>
  </footer>

  <section class="help-card">
    <h2 class="help-title">TROUBLESHOOTING STEPS:</h2>
    <ul class="help-list">
      <li>This screen should only be visible for a short time on boot.</li>
      <li>If this screen stays visible for more than a minute:
        <ul>
          <li>Verify that the Wi-Fi Access Point (AP) powers up when this system does (indicated by a green light on the side of the AP).</li>
          <li>Check the Ethernet cable between this system and the AP for damage, and replace it if necessary.</li>
          <li>Power-cycle this system and wait for it to reboot fully.</li>
          <li>If the issue persists, contact KTWG support for further assistance.</li>
        </ul>
      </li>
    </ul>
  </section>
</main>
</body>
</html>
```